Website to design and sell sundials: www.gnomonvale.com

We have a website that creates a free paper sundial, we want to migrate from this not profit free website to a website where we will continue offering the free paper sundial model but We will also offer a manufactured sundial and sell it.
In order to understand the project, please visit:
http://www.gnomonvale.com/vertical/sundial.html and
http://www.torvel.net/landing/

The website user journey should be redesigned, including the phases that are,
select language
Show product give info
Creation/edit sundial (could be one or more phases)
View created sundial
Buy sundial.

May some of them could be combined or splitted, what It have more sense.

Requirements
Must have
• A description page user journey offering freemium paper sundial and physical sundial to sell.
• A sundial creation page for "free" paper sundial
• A result page for paper sundial
• A sell page for physical

```html
<!DOCTYPE html>
<html lang="en">
<head>
<meta charset="utf-8">
<title>GnomonVale.com – Editor Page</title>
<link href="https://fonts.googleapis.com/css2?family=Raleway:wght@400;500;600&family=Varela+Round&display=swap" rel="stylesheet">
<style>
:root{
  --red:#c3141a;
  --orange:#f9a83c;
  --orange-deep:#f0922a;
  --dark:#3b3b3b;
  --text:#333;
  --white:#fff;
  --map-sea:#a9c7de;
  --map-land:#b9c7a2;
  --line:#c9c9c9;
}
*{box-sizing:border-box;margin:0;padding:0}
html,body{width:772px;height:1200px;overflow:hidden}
body{position:relative;font-family:'Raleway',sans-serif;color:var(--text);background:var(--white)}
.abs{position:absolute}
/* header */
.site-header{left:0;top:0;width:772px;height:64px;border-bottom:2px solid var(--red);background:var(--white)}
.brand{left:64px;top:22px;display:flex;align-items:center;gap:8px;font-size:21px;font-weight:500;color:var(--red)}
.brand .dot{width:12px;height:12px;border-radius:50%;background:var(--red)}
.nav{font-size:10px;top:31px;color:var(--text)}
.nav.active{color:var(--red)}
.nav-swoosh{left:555px;top:38px}
/* map */
.map{left:0;top:66px}
.map-title{left:0;top:200px;width:772px;text-align:center;font-family:'Varela Round',sans-serif;font-size:30px;color:var(--red);-webkit-text-stroke:1px var(--white);font-weight:700}
.zoom{left:744px;width:16px;height:16px;background:var(--white);border:1px solid #ccc;font-size:11px;text-align:center;line-height:14px;color:#666}
/* location */
.location{left:0;top:352px;width:772px;height:330px}
.section-title{width:772px;left:0;text-align:center;font-family:'Varela Round',sans-serif;font-size:22px;font-weight:700;display:flex;justify-content:center;align-items:center;gap:10px}
.section-title .dot{width:10px;height:10px;border-radius:50%}
.loc-title{top:412px;color:var(--white)}
.loc-title .dot{background:var(--white)}
.intro{left:0;width:772px;text-align:center;font-size:8.5px;color:var(--white);line-height:17px;top:456px}
.field{border:1px solid rgba(255,255,255,.85);border-radius:2px;height:27px;color:var(--white);font-size:10px;padding:7px 7px;background:transparent}
.label-w{font-size:10.5px;color:var(--white)}
.go{left:501px;top:512px;width:34px;height:27px;background:var(--red);color:var(--white);font-size:9px;text-align:center;line-height:27px;border-radius:2px}
/* options */
.opt-title{top:706px;color:var(--red)}
.opt-title .dot{background:var(--red)}
.lbl{font-size:9px;color:var(--text);width:151px;left:0;text-align:right}
.radio{width:7px;height:7px;border:1px solid #aaa;border-radius:50%;left:162px}
.radio.on{background:radial-gradient(#666 40%,#fff 45%)}
.check{width:7px;height:7px;border:1px solid #aaa;left:162px;border-radius:1px}
.box{border:1px solid var(--line);border-radius:2px;font-size:8.5px;padding:6px 5px;color:var(--text)}
.create{left:159px;top:935px;width:89px;height:25px;background:var(--red);color:var(--white);font-size:9.5px;text-align:center;line-height:25px;border-radius:2px}
.divider{left:352px;top:758px;width:1px;height:212px;background:#ddd}
.photo{border:1px solid #ddd;padding:2px;width:160px;height:110px}
.photo div{width:100%;height:100%}
.choice{font-size:11px;color:var(--text);top:886px}
/* footer */
.footer{left:0;top:1002px;width:772px;height:166px;background:var(--dark)}
.foot-brand{left:0;width:772px;top:1032px;display:flex;justify-content:center;align-items:center;gap:8px;font-size:18px;font-weight:500;color:var(--white)}
.foot-brand .dot{width:11px;height:11px;border-radius:50%;background:var(--white)}
.foot-rule{left:112px;top:1072px;width:549px;height:1px;background:#555}
.foot-links{left:112px;top:1090px;width:549px;display:flex;justify-content:space-between;font-size:10.5px;color:var(--white)}
.social{width:23px;height:23px;border:1.5px solid var(--white);border-radius:50%;top:1127px}
.bottom-bar{left:0;top:1168px;width:772px;height:32px;background:linear-gradient(var(--orange),var(--orange-deep));font-size:9px;color:var(--white)}
</style>
</head>
<body>

<header class="site-header abs">
  <div class="brand abs"><span class="dot"></span>GnomonVale.com</div>
  <span class="nav active abs" style="left:395px">Introduction</span>
  <span class="nav abs" style="left:474px">Create Sundial</span>
  <span class="nav abs" style="left:570px">Editor Page</span>
  <span class="nav abs" style="left:658px">Contact Us</span>
  <svg class="nav-swoosh abs" width="82" height="18" viewBox="0 0 82 18"><path d="M2 4 Q41 22 80 4 Q41 12 2 4Z" fill="var(--red)"/></svg>
</header>

<svg class="map abs" width="772" height="316" viewBox="0 0 772 316" role="img" aria-label="Road map of Europe, Africa and Asia for choosing the sundial location">
  <defs>
    <linearGradient id="land" x1="0" y1="0" x2="1" y2="1">
      <stop offset="0" stop-color="#c2cfb0"/><stop offset=".6" stop-color="#b6c59a"/><stop offset="1" stop-color="#d4cfae"/>
    </linearGradient>
  </defs>
  <path d="M0 0H772V288Q386 330 0 288Z" fill="url(#land)"/>
  <path d="M0 0H772V288Q386 330 0 288Z" fill="var(--map-sea)" opacity=".35"/>
</svg>
<div class="map-title abs">Sundial Location</div>
<div class="zoom abs" style="top:310px">•</div>
<div class="zoom abs" style="top:327px">+</div>
<div class="zoom abs" style="top:344px;height:10px">–</div>

<section class="location abs" aria-label="Sundial location">
  <svg class="abs" style="left:0;top:0" width="772" height="330" viewBox="0 0 772 330">
    <defs>
      <radialGradient id="burst" cx=".5" cy=".35" r=".7">
        <stop offset="0" stop-color="#fbbc62"/><stop offset="1" stop-color="var(--orange)"/>
      </radialGradient>
    </defs>
    <path d="M0 0Q386 52 772 0V330H0Z" fill="url(#burst)"/>
    <path d="M0 0Q386 52 772 0" fill="none" stroke="var(--red)" stroke-width="2"/>
  </svg>
</section>
<h2 class="section-title loc-title abs"><span class="dot"></span>Sundial location</h2>
<p class="intro abs">Select the location where you want to place your paper sundial, mark a line along building wall where you want to put it.<br>Write your address and press Go! (e.g. Market square, Torvel)</p>
<div class="field abs" style="left:236px;top:512px;width:255px"></div>
<div class="go abs">GO</div>
<span class="label-w abs" style="left:142px;top:574px">Longitude:</span>
<div class="field abs" style="left:199px;top:567px;width:79px">0</div>
<span class="label-w abs" style="left:311px;top:574px">Latitude:</span>
<div class="field abs" style="left:359px;top:567px;width:79px">0</div>
<span class="label-w abs" style="left:466px;top:574px">Wall declination:</span>
<div class="field abs" style="left:550px;top:567px;width:79px">0</div>
<span class="label-w abs" style="left:142px;top:632px">Now select the face of the building:</span>
<span class="label-w abs" style="left:318px;top:632px">Face:</span>
<div class="field abs" style="left:350px;top:624px;width:79px">A<svg class="abs" style="right:7px;top:10px" width="8" height="6"><path d="M0 0H8L4 6Z" fill="#fff"/></svg></div>

<h2 class="section-title opt-title abs"><span class="dot"></span>Sundial Options</h2>
<span class="lbl abs" style="top:771px">Banner:</span>
<div class="box abs" style="left:159px;top:765px;width:106px;height:22px;padding:4px 5px">Paper sundial</div>
<span class="lbl abs" style="top:804px">Solar Time:</span><span class="radio abs" style="top:806px"></span>
<span class="lbl abs" style="top:821px">Civil Time:</span><span class="radio on abs" style="top:823px"></span>
<span class="lbl abs" style="top:843px">Daylight Saving Time:</span><span class="check abs" style="top:845px"></span>
<span class="lbl abs" style="top:873px">Timezone:</span>
<div class="box abs" style="left:159px;top:867px;width:172px;height:22px;padding:5px 5px">(GMT+999) LOCAL TIME (SOLAR TIME)<svg class="abs" style="right:5px;top:8px" width="6" height="5"><path d="M0 0H6L3 5Z" fill="#333"/></svg></div>
<span class="lbl abs" style="top:909px">Equation of time:</span><span class="check abs" style="top:911px"></span>
<div class="create abs">Create Sundial</div>
<div class="divider abs"></div>
<div class="photo abs" style="left:375px;top:766px"><div role="img" aria-label="Photo of a paper sundial fixed on a brick wall" style="background:linear-gradient(90deg,#3e4a3f 0 25%,#a8614a 25%)"></div></div>
<div class="photo abs" style="left:549px;top:766px"><div role="img" aria-label="Photo of a paper sundial on a window facing a terrace" style="background:linear-gradient(90deg,#2a2a26 0 30%,#c9b7a0 30% 70%,#9aa6ae 70%)"></div></div>
<span class="radio on abs" style="left:376px;top:890px"></span><span class="choice abs" style="left:389px">Wall sundial</span>
<span class="radio abs" style="left:549px;top:890px"></span><span class="choice abs" style="left:562px">Window sundial</span>

<footer class="footer abs"></footer>
<div class="foot-brand abs"><span class="dot"></span>GnomonVale.com</div>
<div class="foot-rule abs"></div>
<nav class="foot-links abs">
  <span>Introduction</span><span>|</span><span>Create Sundial</span><span>|</span><span>To Do List</span><span>|</span><span>Sundial Samples</span><span>|</span><span>Contact Us</span>
</nav>
<span class="social abs" style="left:318px"></span>
<span class="social abs" style="left:355px"></span>
<span class="social abs" style="left:393px"></span>
<span class="social abs" style="left:430px"></span>
<div class="bottom-bar abs">
  <span class="abs" style="left:0;width:772px;text-align:center;top:10px">Copyrights 2016. GnomonVale. All rights reserved</span>
  <span class="abs" style="left:734px;top:9px">c 20</span>
</div>
</body>
</html>
```